Redesign current business card for food company

i would like to redesign my business card. our company is food company, our product range from chips, juices, milk and etc (mostly dried food stuff).
I want o keep same logo but , the rest is open to new design.
you can check at our website about our company www.orvelpantry.com

Target Market(s)

most of food company

Industry/Entity Type

Business

Contact Information for Business Card

I want to keep more to blue color...

Colors
3176b5
abd036

Requirements
Must have
• our old logo
Nice to have
• we do not mind to have nice material on bus card in order to accomplish nice design. for example: using spot uv, embossed and etc.

```html
<!DOCTYPE html>
<html lang="en">
<head>
<meta charset="utf-8">
<title>Orvel Business Card</title>
<link href="https://fonts.googleapis.com/css2?family=Source+Sans+3:wght@400;600;700&display=swap" rel="stylesheet">
<style>
  :root {
    --page-bg: #ece9e6;
    --card-white: #ffffff;
    --brand-blue: #1f6fb5;
    --brand-blue-light: #2a8fd6;
    --brand-blue-deep: #1a5ea6;
    --name-ink: #2b3440;
    --accent-yellow: #f6c51c;
    --text-white: #ffffff;
    --shadow: rgba(0, 0, 0, 0.18);
  }
  * { margin: 0; padding: 0; box-sizing: border-box; }
  html, body { width: 1200px; height: 900px; overflow: hidden; }
  body {
    background: var(--page-bg);
    font-family: "Source Sans 3", "Myriad Pro", sans-serif;
    position: relative;
  }
  .card {
    position: absolute;
    width: 588px;
    height: 365px;
    background: var(--card-white);
    box-shadow: 0 6px 18px var(--shadow);
    overflow: hidden;
  }
  .card--front { left: 78px; top: 33px; }
  .card--back { left: 389px; top: 506px; width: 565px; height: 350px; }

  .company-name {
    position: absolute;
    left: 0; right: 0;
    text-align: center;
    color: var(--name-ink);
    font-weight: 600;
    font-size: 60px;
    letter-spacing: 10px;
    line-height: 1;
    text-transform: uppercase;
  }
  .card--front .company-name { top: 78px; }
  .card--back .company-name { top: 66px; font-size: 56px; }

  .front-bands { position: absolute; left: 0; top: 0; width: 588px; height: 365px; }

  .contact-list {
    position: absolute;
    left: 26px; top: 258px;
    list-style: none;
    color: var(--text-white);
    font-size: 16px;
    line-height: 21px;
  }
  .contact-list li { display: flex; align-items: center; gap: 7px; }
  .contact-list svg { width: 11px; height: 11px; fill: var(--text-white); }

  .person {
    position: absolute;
    right: 32px; top: 253px;
    text-align: right;
    color: var(--text-white);
    font-size: 16px;
    line-height: 23px;
  }
  .person__name { font-weight: 700; font-size: 19px; }

  .website {
    position: absolute;
    top: 147px; left: 0; right: 0;
    text-align: center;
    color: var(--brand-blue-deep);
    font-weight: 700;
    font-size: 14px;
  }
  .product-strip {
    position: absolute;
    left: 0; right: 0; bottom: 0;
    height: 155px;
    background: linear-gradient(90deg, #c9dfa0 0%, #f3d35a 30%, #f7d24a 55%, #f1b53a 70%, #b7cf8a 82%, #f9d84a 100%);
    -webkit-mask: linear-gradient(to bottom, transparent 0%, #000 35%);
            mask: linear-gradient(to bottom, transparent 0%, #000 35%);
  }
</style>
</head>
<body>

<section class="card card--front" aria-label="Business card front">
  <svg class="front-bands" viewBox="0 0 588 365" aria-hidden="true">
    <defs>
      <linearGradient id="blueBand" x1="0" y1="0" x2="0" y2="1">
        <stop offset="0" stop-color="#2a8fd6"/>
        <stop offset="1" stop-color="#1a5ea6"/>
      </linearGradient>
    </defs>
    <polygon points="0,199 402,199 383,225 0,225" fill="#f6c51c"/>
    <polygon points="0,227 386,227 414,191 588,191 588,365 0,365" fill="url(#blueBand)"/>
    <polygon points="0,227 386,227 414,191 588,191 588,193 415,193 387,229 0,229" fill="#ffffff" opacity="0.35"/>
  </svg>

  <p class="company-name">Orvel</p>

  <ul class="contact-list">
    <li><svg viewBox="0 0 12 12"><path d="M1 4c0-2 2-3 5-3s5 1 5 3l-2 1-1-1H4L3 5zM2 6h8l1 5H1z"/></svg>555 014 2288</li>
    <li><svg viewBox="0 0 12 12"><path d="M3 1h5v3H3zM1 4h10v7H1zM3 6h2v1H3zm0 2h2v1H3zm4-2h2v3H7z"/></svg>555 014 2277</li>
    <li><svg viewBox="0 0 12 12"><path d="M3 0h6v12H3zM4 1.5v8h4v-8z"/></svg>555 018 4467</li>
    <li><svg viewBox="0 0 12 12"><path d="M0 2h12v8H0zM1 3l5 4 5-4z"/></svg>daniel@orvelpantry.com</li>
  </ul>

  <div class="person">
    <p class="person__name">Daniel Hartono</p>
    <p class="person__title">President</p>
    <p>418 W Birch Ave</p>
    <p>Larkfield CA 91700</p>
  </div>
</section>

<section class="card card--back" aria-label="Business card back">
  <p class="company-name">Orvel</p>
  <p class="website">www.orvelpantry.com</p>
  <div class="product-strip" role="img" aria-label="Illustrated row of products and summer items: beach umbrella, pineapple, rainbow, cheese, crackers, juice splash, mango, avocado, parasol, sun and beach ball"></div>
</section>

</body>
</html>
```